Investment company needing business card

We are wanting a business card which looks sharp and easy on the eye. We are thinking of having a business card with the logo embossed on it, to really make it stand out. We will only have a small amount of information of the business card, person's name, position, email address and phone number

Contact Information for Business Card

Danielle Frost
Executive Assistant
+64 21 473 5162
danielf@harwickpartners.co.nz

Requirements
Must have
• Embossed logo
Should not have
• Not to be busy

```html
<!DOCTYPE html>
<html lang="en">
<head>
<meta charset="utf-8">
<title>Harwick Partners — Business Card</title>
<link rel="stylesheet" href="https://fonts.googleapis.com/css2?family=Lato:wght@400;700;900&display=swap">
<style>
  :root {
    --bg: #2b2b2d;
    --card: #ffffff;
    --green: #22b573;
    --grey: #6b6b6e;
    --white: #ffffff;
  }
  * { margin: 0; padding: 0; box-sizing: border-box; }
  html, body { width: 1200px; height: 880px; overflow: hidden; }
  body {
    background: var(--bg);
    font-family: "Lato", sans-serif;
    position: relative;
  }
  .card {
    position: absolute;
    left: 300px;
    width: 600px;
    height: 343px;
    background: var(--card);
    border-radius: 18px;
    overflow: hidden;
    box-shadow: 0 10px 30px rgba(0,0,0,0.45);
  }
  .card--front { top: 64px; }
  .card--back { top: 472px; }

  .brand {
    position: absolute;
    display: flex;
    align-items: center;
    gap: 14px;
  }
  .brand__mark {
    width: 46px;
    height: 46px;
    background: var(--green);
    border-radius: 6px;
    flex: none;
  }
  .brand__name {
    color: var(--green);
    font-weight: 900;
    text-transform: uppercase;
    line-height: 1;
    letter-spacing: 0.04em;
  }
  .brand__name span { display: block; }
  .brand__name .brand__sub { font-size: 0.55em; letter-spacing: 0.32em; margin-top: 6px; }

  .card--front .brand { left: 50%; top: 50%; transform: translate(-50%, -50%); }
  .card--front .brand__name { font-size: 40px; }

  .card--back .brand { left: 40px; top: 48px; }
  .card--back .brand__mark { width: 40px; height: 40px; }
  .card--back .brand__name { font-size: 32px; }

  .side-panel { position: absolute; inset: 0; width: 600px; height: 343px; }

  .contact {
    position: absolute;
    right: 30px;
    top: 132px;
    text-align: right;
    color: var(--white);
  }
  .contact__name { font-size: 19px; font-weight: 700; }
  .contact__role { font-size: 14px; font-weight: 400; margin-bottom: 16px; }
  .contact__line {
    display: flex;
    justify-content: flex-end;
    align-items: center;
    gap: 8px;
    font-size: 14px;
    margin-top: 7px;
  }
  .contact__icon { width: 18px; height: 18px; flex: none; }
</style>
</head>
<body>

  <section class="card card--front" aria-label="Card front">
    <div class="brand">
      <div class="brand__mark"></div>
      <div class="brand__name"><span>Harwick</span><span class="brand__sub">Partners</span></div>
    </div>
  </section>

  <section class="card card--back" aria-label="Card back">
    <svg class="side-panel" viewBox="0 0 600 343" aria-hidden="true">
      <path fill="var(--green)" d="M600 0 L430 0 C380 110 370 240 310 343 L600 343 Z"/>
      <path fill="none" stroke="var(--grey)" stroke-width="4" d="M410 0 C360 110 350 240 290 343"/>
    </svg>

    <div class="brand">
      <div class="brand__mark"></div>
      <div class="brand__name"><span>Harwick</span><span class="brand__sub">Partners</span></div>
    </div>

    <div class="contact">
      <div class="contact__name">Danielle Frost</div>
      <div class="contact__role">Executive Assistant</div>
      <div class="contact__line">
        <span>+64 21 473 5162</span>
        <svg class="contact__icon" viewBox="0 0 18 18" aria-hidden="true">
          <circle cx="9" cy="9" r="8" fill="none" stroke="var(--white)" stroke-width="1.4"/>
          <rect x="6.2" y="4" width="5.6" height="10" rx="1" fill="none" stroke="var(--white)" stroke-width="1.3"/>
          <line x1="8" y1="12" x2="10" y2="12" stroke="var(--white)" stroke-width="1.2"/>
        </svg>
      </div>
      <div class="contact__line">
        <span>danielf@harwickpartners.co.nz</span>
        <svg class="contact__icon" viewBox="0 0 18 18" aria-hidden="true">
          <circle cx="9" cy="9" r="8" fill="none" stroke="var(--white)" stroke-width="1.4"/>
          <rect x="4.5" y="5.8" width="9" height="6.4" fill="none" stroke="var(--white)" stroke-width="1.2"/>
          <polyline points="4.5,5.8 9,9.6 13.5,5.8" fill="none" stroke="var(--white)" stroke-width="1.2"/>
        </svg>
      </div>
    </div>
  </section>

</body>
</html>
```